web Design for Architecture and Interior Design Firm

This is a complete redesign of an architecture and interior design firm.( http://www.qlbrankworks.com )
We have established a new look-n-feel for them and need to apply it to the new site/new architecture. Wireframes attached with logo and PDF of new brochure.
This will require a quck turn-around. The client is expecting a very modern design with web 2.0 in mind.
Again very quick turn-around! If you cannot commit to a Friday deliverable, do not bid! Must be completed by no later than Friday!

```html
<!DOCTYPE html>
<html lang="en">
<head>
<meta charset="utf-8">
<title>Qlbrank Works Design Studios</title>
<link href="https://fonts.googleapis.com/css2?family=PT+Sans:wght@400;700&family=Arimo:wght@400;700&family=Tinos&display=swap" rel="stylesheet">
<style>
:root{
  --page-bg:#c9c9c9;
  --white:#ffffff;
  --brown:#675c49;
  --brand-red:#c0122f;
  --ink:#2b2b2b;
  --grey-band:#e6e6e6;
  --contact-bg:#656565;
  --footer-bg:#e4e4e4;
  --photo-a:#8a6a3a;
  --photo-b:#c99a52;
}
*{margin:0;padding:0;box-sizing:border-box}
html,body{width:1200px;height:843px;overflow:hidden}
body{background:var(--page-bg);position:relative;font-family:"Arimo",Arial,sans-serif;color:var(--ink)}
.header-bg{position:absolute;left:0;top:0;width:1200px;height:131px;background:linear-gradient(#e2e2e2,#fdfdfd 60%,#ffffff)}
.page{position:absolute;left:150px;top:131px;width:900px;height:684px;background:var(--white)}
.abs{position:absolute}
.brand{position:absolute;left:169px;top:46px;display:flex;align-items:center;gap:10px}
.brand-mark{width:12px;height:12px;background:var(--brown)}
.brand-name{font-family:"PT Sans",sans-serif;font-weight:400;font-size:36px;letter-spacing:.5px;color:var(--brown);line-height:1}
.contact-box{position:absolute;left:769px;top:0;width:281px;height:75px;background:var(--contact-bg);border-radius:0 0 4px 4px;color:var(--white);font-family:"PT Sans",sans-serif;font-size:14px}
.contact-box p{position:absolute;left:40px}
.contact-box b{color:#000;font-size:15px}
.nav{position:absolute;top:103px;left:0;font-family:"PT Sans",sans-serif;font-size:14px;color:var(--ink)}
.nav span{position:absolute;white-space:nowrap}
.nav .active::before{content:"";position:absolute;left:0;top:-8px;width:33px;height:3px;background:var(--brand-red)}
.caret{font-size:8px;margin-left:4px}
.stage{position:absolute;left:0;top:0}
.hero-title{position:absolute;left:169px;top:173px;font-family:"PT Sans",sans-serif;font-size:22px;font-weight:400;color:var(--white)}
.hero-list{position:absolute;left:187px;top:213px;list-style:none;color:var(--white);font-size:13.5px;line-height:15px}
.hero-list li{margin-bottom:7.5px}
.btn{position:absolute;width:111px;height:29px;border-radius:15px;background:linear-gradient(#d4334c,#a50d27 55%,#8e0a20);color:var(--white);font-size:14px;text-align:center;line-height:29px;font-family:"Arimo",sans-serif}
.slide-count{position:absolute;left:437px;top:389px;font-family:"Tinos",serif;font-size:14px;color:#111}
.slide-count em{font-style:normal;color:var(--brand-red)}
.welcome-title{position:absolute;left:169px;top:435px;font-family:"PT Sans",sans-serif;font-size:25px;color:var(--ink);font-weight:400}
.welcome-title span{color:var(--brand-red)}
.welcome-copy{position:absolute;left:169px;top:480px;width:585px;font-size:11.3px;line-height:16.8px;color:#1e1e1e}
.welcome-copy p{margin-bottom:16.8px}
.services-title{position:absolute;left:810px;top:395px;font-family:"PT Sans",sans-serif;font-size:17px;font-weight:400;color:var(--white)}
.services-rule{position:absolute;left:810px;top:423px;width:221px;height:1px;background:#948a78}
.services-copy{position:absolute;left:810px;top:437px;width:215px;font-size:11.3px;line-height:17px;color:var(--white)}
.services-list{position:absolute;left:824px;top:504px;list-style:none;color:var(--white);font-size:11.3px}
.services-list li{height:22.5px;padding-left:20px;position:relative}
.services-list li::before{content:"";position:absolute;left:0;top:2px;width:6px;height:10px;border-radius:6px 0 0 6px;background:var(--white)}
.footer{position:absolute;left:150px;top:691px;width:900px;height:124px;background:var(--footer-bg);border-top:1px solid #9a9a9a}
.footer-col{position:absolute;top:12px;font-size:11.3px;color:#2a2a2a}
.footer-col h4{font-size:12px;font-weight:700;height:29px}
.footer-col li{list-style:none;height:17px}
.footer-col .current{color:var(--brand-red)}
.footer-rule{position:absolute;left:19px;top:34px;width:619px;height:1px;background:#666}
.footer-brand{position:absolute;left:670px;top:40px;display:flex;align-items:center;gap:8px}
.footer-brand .brand-mark{width:9px;height:9px}
.footer-brand .brand-name{font-size:27px}
.copyright{position:absolute;left:670px;top:96px;font-size:10px;color:#333}
.copyright span{color:#7a6440}
</style>
</head>
<body>
<div class="header-bg"></div>
<div class="page"></div>

<div class="brand">
  <div class="brand-name">Qlbrank Works</div>
  <div class="brand-mark"></div>
</div>

<div class="contact-box">
  <svg class="abs" style="left:38px;top:8px" width="20" height="20" viewBox="0 0 20 20"><circle cx="10" cy="10" r="9" fill="none" stroke="#fff" stroke-width="1.3"/><path d="M7 5c-1 1-1 3 1 6s4 4 5 4l1-2-2-1-1 1c-1-.5-2-2-2.5-3l1-1-1-2z" fill="#fff"/></svg>
  <p style="top:10px;left:67px">Call Us: <b>555.014.0270 x121</b></p>
  <p style="top:36px;left:30px;font-size:17px">@</p>
  <p style="top:38px;left:55px">email: <b>admin@qlbrankworks.com</b></p>
</div>

<nav class="nav">
  <span class="active" style="left:570px">Home</span>
  <span style="left:645px">About Us<span class="caret">▼</span></span>
  <span style="left:738px">Services<span class="caret">▼</span></span>
  <span style="left:827px">Portfolio</span>
  <span style="left:915px">News<span class="caret">▼</span></span>
  <span style="left:987px">Contact</span>
</nav>

<svg class="stage" width="1200" height="843" viewBox="0 0 1200 843">
  <defs>
    <linearGradient id="photoTone" x1="0" x2="1" y1="0" y2="1">
      <stop offset="0" stop-color="#b7b2a8"/>
      <stop offset=".45" stop-color="var(--photo-a)"/>
      <stop offset="1" stop-color="var(--photo-b)"/>
    </linearGradient>
  </defs>
  <rect x="478" y="131" width="572" height="31" fill="var(--grey-band)"/>
  <rect x="430" y="162" width="620" height="220" fill="url(#photoTone)" role="img" aria-label="Photograph of the Harlow Bennet studio reception with lounge chairs and wood panelling"/>
  <polygon points="426,382 797,382 797,412 420,412" fill="var(--grey-band)"/>
  <polygon points="150,131 478,131 426,412 150,412" fill="var(--brown)"/>
  <polygon points="797,382 1050,382 1050,663 741,663" fill="var(--brown)"/>
  <polygon points="760,390 777,397 760,404" fill="var(--brand-red)"/>
  <polygon points="766,390 778,397 766,404" fill="#6a6a6a" opacity=".6"/>
</svg>

<h1 class="hero-title">Harlow Bennet, Arlington, VA</h1>
<ul class="hero-list">
  <li>Technical spaces for video production/<br>post production company</li>
  <li>10,000 SF</li>
  <li>Secure information area</li>
  <li>Editing suites and studios</li>
  <li>Demonstration lab</li>
  <li>Open ceilings</li>
</ul>
<div class="btn" style="left:287px;top:367px">Read More</div>

<div class="slide-count">1/ 10 | <em>Slide 1</em></div>

<h2 class="welcome-title">Welcome to <span>Qlbrank Works Design Studios</span></h2>
<div class="welcome-copy">
  <p>Founded in 1985 as Plancraft Inc., Qlbrank Works Design Studios is a full-service architecture and interior design firm serving the planning and design needs of facility managers, property managers and tenants in the commercial real estate market.</p>
  <p>We integrate engineering considerations into creative architectural design solutions through our in-house strategic alliance with Dorsey Vance &amp; Associates Engineering. This comprehensive approach to design gives our clients the best value for their build-out dollar, while ensuring the highest level of quality and coordination between the architectural and engineering drawings and specification.</p>
  <p>Our on-going goal is to develop long lasting relationships where we are valued, respected and trusted.</p>
</div>

<h3 class="services-title">Services</h3>
<div class="services-rule"></div>
<p class="services-copy">We are committed to providing services that result in environments that meet our clients' needs and desired image.</p>
<ul class="services-list">
  <li>Architectural</li>
  <li>Engineering</li>
  <li>Interior Design</li>
  <li>Facility Management</li>
</ul>
<div class="btn" style="left:812px;top:611px">Read More</div>

<footer class="footer">
  <div class="footer-col" style="left:19px"><h4>Home</h4></div>
  <div class="footer-col" style="left:114px"><h4>About Us</h4><ul><li>DVA Alliance</li><li>History</li><li>Firm Principals</li><li>Our Mission</li></ul></div>
  <div class="footer-col" style="left:255px"><h4>Services</h4><ul><li class="current">Architectural</li><li>Engineering</li><li>Interior Design</li><li>Facility Management</li></ul></div>
  <div class="footer-col" style="left:429px"><h4>Portfolio</h4></div>
  <div class="footer-col" style="left:539px"><h4>News</h4><ul><li>Newsletter</li><li>Awards</li><li>Firm Events</li><li>20th Anniversary</li></ul></div>
  <div class="footer-rule"></div>
  <div class="footer-brand">
    <div class="brand-name">Qlbrank Works</div>
    <div class="brand-mark"></div>
  </div>
  <div class="copyright">Copyright 2011. <span>Qlbrank Works Design Studios.</span></div>
</footer>
</body>
</html>
```